Wordpress Site Design for a Horror and Action Movie Production Company

We need a re-design/facelift of our website: https://k42t.pagecraft.io
The structure of the website could remain the same, but it needs to look and feel BETTER!

We would like the website coded in Wordpress so that it can be easily updated bu us, via adding new projects and new projects' info.

We specialize in Action, Horror, and Sci-Fi Genre. That being said, we don't want the website to look like it's a themed park with haunted houses. It should still be sharp and professional, as after all - it is a business for us!

Target Market(s)

Film Distribution Companies (B2B), as well as general audience that likes movies

Industry/Entity Type

Movie Production

Coding

Coded - Design and coding required

Number of Pages Required

5+ page

Font styles to use
Sans Serif

Colors

Designer to choose colors to be used in the design.

Requirements
Must have
• - PROJECTS page
• - Each PROJECT has a sub-page with project info/updates (up dates could be in a form of a WP post, ideally a template that we can use to update and create new PROJECT pages, with text, poster, and video link (trailer))
• - NEWS page that chronologically lists updates from all PROJECTS (could be done via WP blog)
• - HOME page would
Nice to have
• Should generally have a dark background.
• Websites we like as a reference of general approach and style:
• https://marbletoq.com
• https://velunpix.com (however this is very image-centric, and we might not have that much imagery at the moment)
• https://www.copperfieldechoandframe.com/other
• https://quennreels.com
Should not have
• We specialize in Action, Horror, and Sci-Fi Genre. That being said, we don't want the website to look like it's a themed park with haunted houses. It should still be sharp and professional, as after all - it is a business for us!

```html
<!DOCTYPE html>
<html lang="en">
<head>
<meta charset="utf-8">
<title>Contact Us – Kiln 42 Media</title>
<link rel="stylesheet" href="https://fonts.googleapis.com/css2?family=Montserrat:wght@800&family=Roboto:wght@400;500&family=Ubuntu:wght@300;400;500&display=swap">
<style>
:root{
  --header-bg:#1a1b23;
  --deep:#0b0c10;
  --section-bg:#1c1d25;
  --panel-left:#5f5f62;
  --panel-right:#2f2f31;
  --footer-bg:#1a1b22;
  --notice-bg:#232327;
  --red:#d9222a;
  --white:#ffffff;
  --ink:#0d0d0f;
  --muted:#8c8d93;
  --map-a:#c9cbd1;
  --map-b:#b7bac2;
}
*{margin:0;padding:0;box-sizing:border-box}
html,body{width:1200px;height:2430px;overflow:hidden}
body{position:relative;background:var(--deep);font-family:"Roboto",sans-serif;color:var(--white)}
.abs{position:absolute}

/* header */
.site-header{left:0;top:0;width:1200px;height:70px;background:var(--header-bg)}
.brand{left:28px;top:0;width:143px;height:66px;background:#111216;display:flex;flex-direction:column;align-items:center;justify-content:center;border-bottom:2px solid #2a2b31}
.brand-name{font-family:"Ubuntu",sans-serif;font-weight:500;font-size:21px;letter-spacing:1px;line-height:1}
.brand-sub{font-family:"Ubuntu",sans-serif;font-weight:500;font-size:9px;letter-spacing:3px;margin-top:4px}
.main-nav{top:0;left:530px;height:70px;display:flex}
.main-nav a{position:relative;display:block;height:70px;line-height:70px;padding:0 21px;font-family:"Roboto",sans-serif;font-weight:500;font-size:14px;letter-spacing:.6px;color:var(--white);text-decoration:none}
.main-nav a.is-active{color:var(--red)}
.main-nav a.is-active::after{content:"";position:absolute;left:27px;right:27px;bottom:2px;height:2px;background:var(--red)}
.nav-arc{left:930px;top:8px}
.search-icon{left:1146px;top:24px}

/* hero */
.hero-map{left:0;top:70px;width:1200px;height:495px;background:linear-gradient(135deg,var(--map-a),var(--map-b) 55%,#c4c1bb)}
.hero-shade{left:0;top:515px;width:1200px;height:50px;background:rgba(30,30,36,.35)}
.hero-title{left:0;top:135px;width:1215px;text-align:center;font-family:"Ubuntu",sans-serif;font-weight:500;font-size:37px}
.hero-pin{left:555px;top:195px}
.red-rule{left:0;top:565px;width:1200px;height:3px;background:var(--red)}

/* section heading */
.contact-heading{left:0;top:620px;width:1200px;height:210px;background:var(--section-bg);border-top:1px solid #22232b}
.heading-arc{left:518px;top:697px}
.heading-title{left:0;top:718px;width:1194px;text-align:center;font-family:"Ubuntu",sans-serif;font-weight:500;font-size:32px}
.heading-rule{left:519px;top:765px;width:153px;height:3px;background:var(--red)}

/* contact panels */
.detail-panel{left:0;top:830px;width:600px;height:727px;background:var(--panel-left)}
.form-panel{left:600px;top:830px;width:600px;height:727px;background:var(--panel-right)}
.detail-title{left:59px;top:922px;font-family:"Montserrat",sans-serif;font-weight:800;font-size:48px;color:var(--ink);letter-spacing:-.5px}
.detail-intro{left:59px;top:1003px;width:520px;font-size:18px;line-height:30px}
.hq-title{left:58px;top:1144px;font-family:"Roboto",sans-serif;font-weight:500;font-size:23px}
.hq-address{left:59px;top:1196px;font-family:"Roboto",sans-serif;font-weight:500;font-size:13.5px;line-height:30px;color:#111}
.contact-list{left:55px;top:1366px;list-style:none}
.contact-list li{display:flex;align-items:center;height:38px;font-size:18px;color:#111}
.contact-list svg{width:28px;margin-right:27px;flex:none}
.field-label{left:744px;font-size:14px;font-weight:500}
.field-line{left:745px;width:388px;height:2px;background:#e8e8e8}
.send-btn{left:738px;top:1418px;width:188px;height:56px;background:var(--red);text-align:center;line-height:56px;font-family:"Ubuntu",sans-serif;font-weight:500;font-size:21px;letter-spacing:.5px;box-shadow:0 8px 18px rgba(0,0,0,.25)}

/* lower map */
.lower-strip{left:0;top:1557px;width:1200px;height:10px;background:var(--deep)}
.location-map{left:0;top:1567px;width:1200px;height:433px;background:linear-gradient(135deg,var(--map-a),var(--map-b) 55%,#c4c1bb)}
.map-foot{left:0;top:2000px;width:1200px;height:8px;background:var(--deep)}

/* footer */
.site-footer{left:0;top:2008px;width:1200px;height:190px;background:var(--footer-bg)}
.copyright{left:0;top:2056px;width:1268px;text-align:center;font-family:"Ubuntu",sans-serif;font-weight:300;font-size:15px;color:var(--muted)}
.disclaimer{left:60px;top:2105px;width:1080px;text-align:center;font-family:"Ubuntu",sans-serif;font-size:12.3px;line-height:24px;color:#e6e6e6}
.notice{left:0;top:2198px;width:1200px;height:232px;background:var(--notice-bg)}
.notice-title{left:0;top:2224px;width:1186px;text-align:center;font-family:"Roboto",sans-serif;font-size:15.5px;letter-spacing:.4px}
.notice-text{left:60px;top:2272px;width:1080px;text-align:center;font-family:"Ubuntu",sans-serif;font-weight:300;font-size:12.3px;line-height:24px;color:#a9a9ae}
</style>
</head>
<body>

<header class="site-header abs">
  <div class="brand abs"><span class="brand-name">KILN 42</span><span class="brand-sub">MEDIA</span></div>
  <nav class="main-nav abs">
    <a href="#">HOME</a><a href="#">ABOUT</a><a href="#">NEWS</a><a href="#">PROJECTS</a><a href="#" class="is-active">CONTACT US</a>
  </nav>
  <svg class="nav-arc abs" width="90" height="10" viewBox="0 0 90 10"><path d="M2 9 Q45 -3 88 9" fill="none" stroke="#d9222a" stroke-width="2.5"/></svg>
  <svg class="search-icon abs" width="22" height="22" viewBox="0 0 22 22"><circle cx="9" cy="9" r="7" fill="none" stroke="#d9222a" stroke-width="2"/><path d="M14 14 L20 20" stroke="#d9222a" stroke-width="2.4" stroke-linecap="round"/></svg>
</header>

<section>
  <div class="hero-map abs" role="img" aria-label="Street map of the neighbourhood around the company headquarters"></div>
  <div class="hero-shade abs"></div>
  <h1 class="hero-title abs">CONTACT US</h1>
  <svg class="hero-pin abs" width="118" height="158" viewBox="0 0 118 158"><path d="M59 2 C26 2 2 27 2 59 C2 92 40 118 59 156 C78 118 116 92 116 59 C116 27 92 2 59 2 Z" fill="#d9222a"/><circle cx="59" cy="58" r="34" fill="#c9cbd1"/></svg>
  <div class="red-rule abs"></div>
</section>

<section>
  <div class="contact-heading abs"></div>
  <svg class="heading-arc abs" width="156" height="18" viewBox="0 0 156 18"><path d="M2 16 Q78 -6 154 16" fill="none" stroke="#9a9ba2" stroke-width="3"/></svg>
  <h2 class="heading-title abs">CONTACT US</h2>
  <div class="heading-rule abs"></div>
</section>

<section>
  <div class="detail-panel abs"></div>
  <h2 class="detail-title abs">CONTACT DETAIL</h2>
  <p class="detail-intro abs">Lorem ipsum dolor sit amet, consectetur adipiscing elit, sed do eiusmod tempor incididunt ut labore et dolore magna aliqua.</p>
  <h3 class="hq-title abs">K42M HEADQUARTERS</h3>
  <address class="hq-address abs" style="font-style:normal">8-4410 LARCHMERE AVE.,<br>HALDEN, ON,<br>R2P4V7,<br>CANADA</address>
  <ul class="contact-list abs">
    <li><svg viewBox="0 0 28 24" height="24"><rect x="1" y="1" width="26" height="22" rx="3" fill="#fff"/><path d="M9 5 C6 8 8 16 15 20 L18 17 L15 14 L13 15 C11 13 10 11 10 9 L12 8 L11 4 Z" fill="#5f5f62"/></svg>+1 (555) 014-XXXXX</li>
    <li><svg viewBox="0 0 28 22" height="22"><rect x="1" y="2" width="26" height="18" fill="none" stroke="#fff" stroke-width="1.6"/><path d="M1 2 L14 13 L27 2 M1 20 L11 11 M27 20 L17 11" fill="none" stroke="#fff" stroke-width="1.4"/></svg>mara@fernlowpost.com</li>
    <li><svg viewBox="0 0 28 30" height="30"><path d="M6 2 L6 24 L11 19 L15 28 L18 27 L14 18 L21 18 Z" fill="#fff"/></svg>&nbsp;www.fernlowpost.com</li>
  </ul>

  <div class="form-panel abs"></div>
  <span class="field-label abs" style="top:1007px">Name</span>
  <div class="field-line abs" style="top:1044px"></div>
  <span class="field-label abs" style="top:1087px">Email</span>
  <div class="field-line abs" style="top:1124px"></div>
  <span class="field-label abs" style="top:1167px">Subject</span>
  <div class="field-line abs" style="top:1204px"></div>
  <span class="field-label abs" style="top:1227px">Message</span>
  <div class="field-line abs" style="top:1372px;left:740px"></div>
  <div class="send-btn abs">SEND</div>
</section>

<div class="lower-strip abs"></div>
<div class="location-map abs" role="img" aria-label="Wide street map showing the headquarters location and surrounding streets"></div>
<div class="map-foot abs"></div>

<footer>
  <div class="site-footer abs"></div>
  <p class="copyright abs">Copyright © 2019 Kiln 42 Media Inc. All rights reserved.</p>
  <p class="disclaimer abs">All the information on this website is published in good faith and for general information purpose only. Kiln 42 Media Inc. does not make any warranties about the completeness, reliability and accuracy of this information. Any action you take upon the information you find on this website is strictly at your own risk. will not be liable for any losses and/or damages in connection with the use of our website.</p>
  <div class="notice abs"></div>
  <h4 class="notice-title abs">SCRIPT AND STORY SUBMISSION NOTICE</h4>
  <p class="notice-text abs">Any unsolicited pitches, outlines, scripts, treatments, etc. will be discarded and will not be read. The purpose of<br>this policy is to avoid any potential misunderstandings if your original work seems similar to something we may already have in development. Please note, if you choose to submit materials regardless of this policy, you acknowledge that you have read our submission policy and understand that by making such a submission, you understand that Kiln 42 Media Inc. has no obligation to you or your submission and that you have no claim whatsoever based on such submission.</p>
</footer>

</body>
</html>
```